Thornbury Building Company - Card Design

I am looking to use the logo designs that you already did for me to develop a business card. I would like the card to have a black background and be double sided. I want white and green logo and text. I have attached an inspiration photo of a look that I like. I would like to use the Vertical Logo attached to take up the full front side of the card. On the back where I have my name and information, I would like to have the horizontal logo or maybe even just the image of the 'A' and trees without the text. I am open, but I am looking for something clean and simple and I want the green to really pop! Additional files can be found under Design #: 58302946

Target Market(s)

Homeowners

Industry/Entity Type

Construction

Contact Information for Business Card

Name: Marcus Thornbury, Title: Project Manager, Phone: 555.274.8136, Email: thornburybuildingcompany@mailvesta.com, address: 487 Larkspur Ln, Larkmoor, CA 95033, Lic# 2468317

Colors
00AB8E
00BBA5
67D7C9
C6EFE9
E9F9F6

Requirements
Nice to have
• I would like to see the logos that I have already got from ArtLoomHub, though I am open to new ones

```html
<!DOCTYPE html>
<html lang="en">
<head>
<meta charset="utf-8">
<title>Thornbury Building Company – Business Card</title>
<link rel="stylesheet" href="https://fonts.googleapis.com/css2?family=Poppins:wght@400;600;700&display=swap">
<style>
  :root {
    --backdrop: #5d5d5f;
    --card: #232323;
    --green: #3dba4e;
    --white: #ffffff;
    --ink-soft: #e9e9e9;
    --emboss: #151515;
    --emboss-ring: #3a3a3a;
  }
  * { margin: 0; padding: 0; box-sizing: border-box; }
  html, body {
    width: 900px; height: 1200px; overflow: hidden;
    background: var(--backdrop);
    font-family: "Poppins", sans-serif;
  }
  .canvas { position: relative; width: 900px; height: 1200px; }
  .card {
    position: absolute; left: 119px; width: 661px; height: 375px;
    background: var(--card);
    box-shadow: 0 10px 18px rgba(0,0,0,.35);
    overflow: hidden;
  }
  .card--front { top: 203px; }
  .card--back { top: 620px; }

  /* Front */
  .front-brand {
    position: absolute; left: 0; right: 0; top: 92px;
    display: flex; flex-direction: column; align-items: center;
  }
  .brand-dot {
    width: 58px; height: 58px; border-radius: 50%;
    background: var(--green); margin-bottom: 18px;
  }
  .brand-name {
    color: var(--white); font-weight: 600; font-size: 34px;
    line-height: 1.12; letter-spacing: 2px; text-align: center;
    text-transform: uppercase;
  }

  /* Back */
  .holder-name {
    position: absolute; left: 29px; top: 46px;
    color: var(--green); font-weight: 700; font-size: 25px;
    letter-spacing: .4px; text-transform: uppercase;
  }
  .holder-title {
    position: absolute; left: 29px; top: 76px;
    color: var(--white); font-size: 15.5px; letter-spacing: .6px;
  }
  .address {
    position: absolute; left: 29px; top: 227px;
    color: var(--ink-soft); font-size: 15.5px; line-height: 24px; letter-spacing: .6px;
  }
  .contact {
    position: absolute; left: 29px;
    display: flex; align-items: center; gap: 6px;
    color: var(--ink-soft); font-size: 15.5px;
  }
  .contact--phone { top: 284px; letter-spacing: 3px; }
  .contact--email { top: 313px; letter-spacing: .5px; font-size: 15px; }
  .contact svg { width: 15px; height: 15px; fill: var(--green); flex: none; }
  .licence {
    position: absolute; left: 426px; top: 315px;
    color: var(--green); font-weight: 700; font-size: 15px; letter-spacing: .3px;
  }
  .emboss-ring {
    position: absolute; left: 370px; top: 77px;
    width: 222px; height: 222px; border-radius: 50%;
    border: 3px solid var(--emboss-ring);
  }
  .emboss-name {
    position: absolute; left: 330px; top: 160px; width: 302px;
    color: var(--emboss); font-weight: 600; font-size: 24px;
    line-height: 1.15; letter-spacing: 1.5px; text-align: center;
    text-transform: uppercase;
  }
</style>
</head>
<body>
<main class="canvas">
  <section class="card card--front" aria-label="Card front">
    <div class="front-brand">
      <span class="brand-dot"></span>
      <p class="brand-name">Thornbury<br>Building Company</p>
    </div>
  </section>

  <section class="card card--back" aria-label="Card back">
    <h1 class="holder-name">Marcus Thornbury</h1>
    <p class="holder-title">Project Manager</p>

    <div class="emboss-ring"></div>
    <p class="emboss-name">Thornbury<br>Building Company</p>

    <p class="address">487 Larkspur Ln, Larkmoor,<br>CA 95033</p>
    <p class="contact contact--phone">
      <svg viewBox="0 0 24 24" aria-hidden="true"><path d="M6.6 10.8a15.1 15.1 0 0 0 6.6 6.6l2.2-2.2a1 1 0 0 1 1-.25 11.4 11.4 0 0 0 3.6.57 1 1 0 0 1 1 1V20a1 1 0 0 1-1 1A17 17 0 0 1 3 4a1 1 0 0 1 1-1h3.5a1 1 0 0 1 1 1c0 1.250.2 2.45.57 3.57a1 1 0 0 1-.25 1z"/></svg>
      555.274.8136
    </p>
    <p class="contact contact--email">
      <svg viewBox="0 0 24 24" aria-hidden="true"><path d="M2 5h20v14H2z M3.5 6.5 12 13l8.5-6.5" stroke="#232323" stroke-width="1.6"/></svg>
      thornburybuildingcompany@mailvesta.com
    </p>
    <p class="licence">Lic# 2468317</p>
  </section>
</main>
</body>
</html>
```